Quote Cards With KB May 2025 for Instagram

I would like to put these quotes over one of the pictures attached; Instagram (new size: 4:5 (1080 x 1350 pixels) One Quote per picture, and I want the quote to be bold or easy to read as well. I provided a few reference graphics that I really like as examples below. In very small letters at the bottom add @KBHarlowOnline

All of the pictures are attached; you can pick any photo and add one quote to it; but no stock photography

```html
<!DOCTYPE html>
<html lang="en">
<head>
<meta charset="utf-8">
<title>Quote Card – KB</title>
<link rel="stylesheet" href="https://fonts.googleapis.com/css2?family=Bebas+Neue&display=swap">
<style>
  :root {
    --night-deep: #1a1420;
    --night-violet: #4a3a5c;
    --night-mauve: #8a6f86;
    --city-blue: #2c3f7a;
    --floor-brown: #2a1f1a;
    --band: rgba(8, 6, 10, 0.86);
    --ink: #ffffff;
  }
  * { margin: 0; padding: 0; box-sizing: border-box; }
  html, body {
    width: 960px;
    height: 1200px;
    overflow: hidden;
    background: var(--night-deep);
  }
  .quote-card {
    position: relative;
    width: 960px;
    height: 1200px;
    overflow: hidden;
    font-family: "Bebas Neue", "Oswald", sans-serif;
    color: var(--ink);
  }
  .photo {
    position: absolute;
    inset: 0;
    background:
      radial-gradient(ellipse 40% 30% at 15% 10%, rgba(210, 170, 190, 0.55), transparent 70%),
      radial-gradient(ellipse 35% 25% at 95% 8%, rgba(200, 160, 190, 0.5), transparent 70%),
      radial-gradient(ellipse 30% 22% at 95% 55%, rgba(60, 110, 200, 0.45), transparent 70%),
      radial-gradient(ellipse 28% 40% at 20% 45%, rgba(20, 16, 22, 0.85), transparent 75%),
      linear-gradient(180deg,
        var(--night-mauve) 0%,
        var(--night-violet) 25%,
        var(--city-blue) 50%,
        var(--night-violet) 66%,
        var(--floor-brown) 78%,
        #1b1411 100%);
  }
  .quote-band {
    position: absolute;
    top: 0;
    left: 394px;
    width: 495px;
    height: 1200px;
    background: var(--band);
  }
  .quote {
    position: absolute;
    top: 134px;
    left: 394px;
    width: 495px;
    text-align: center;
    font-size: 78px;
    font-weight: 400;
    letter-spacing: 0.5px;
  }
  .quote-block { line-height: 77px; }
  .quote-block + .quote-block { margin-top: 58px; }
  .quote-block.promise { line-height: 89px; margin-top: 48px; }
  .handle {
    position: absolute;
    top: 1100px;
    left: 394px;
    width: 495px;
    text-align: center;
    font-size: 32px;
    letter-spacing: 0.3px;
  }
</style>
</head>
<body>
  <main class="quote-card">
    <div class="photo" role="img" aria-label="Photo of KB standing in a black sheer top and black jeans in front of a window overlooking a city skyline at night"></div>
    <div class="quote-band"></div>
    <h1 class="quote">
      <div class="quote-block">What worked<br>in your 30s<br>won’t work now.</div>
      <div class="quote-block">Here’s what<br>actually does.</div>
      <div class="quote-block promise">Drop 30 pounds<br>in 3 months.</div>
    </h1>
    <p class="handle">@KBHARLOWONLINE</p>
  </main>
</body>
</html>
```